BRISKEL Need a luxury modern business card designed.

Need a luxury modern business card designed. refer to the uploaded files for the company name and logo in the zip file under source files. i will making my descion on monday. so please send in before then so if we need to edit we will have the time. we have a trade show coming up and im on a deadline for printer.

Target Market(s)

high end clients

Contact Information for Business Card

Company nAme and logo. Tobias Fennick Co-Founder / Project Manager Office # 555-318-7094 Cell # 555-642-1586 BRISKEL.CA Tobias@briskel-example.ca

Font styles to use
Other font styles liked:
• Modern

Requirements
Must have
• Company name and logo, contact info, using the black, gold and white color scheme.

```html
<!DOCTYPE html>
<html lang="en">
<head>
<meta charset="utf-8">
<title>BRISKEL Business Card</title>
<link rel="stylesheet" href="https://fonts.googleapis.com/css2?family=Josefin+Sans:wght@300&family=Montserrat:wght@400;600&display=swap">
<style>
  :root {
    --stage: #161616;
    --card: #2e2e2e;
    --gold: #a89a66;
    --white: #ffffff;
    --soft-white: #ececec;
  }
  * { box-sizing: border-box; margin: 0; padding: 0; }
  html, body {
    width: 1200px; height: 900px; overflow: hidden;
    background: var(--stage);
  }
  .canvas {
    position: relative; width: 1200px; height: 900px;
  }
  .card {
    position: absolute; left: 250px; width: 700px; height: 400px;
    background: var(--card); overflow: hidden;
  }
  .card--back { top: 40px; }
  .card--front { top: 470px; }

  .wordmark {
    position: absolute; left: 0; right: 0; text-align: center;
    font-family: "Josefin Sans", sans-serif; font-weight: 300;
    color: var(--white); letter-spacing: 12px;
  }
  .card--back .wordmark { top: 170px; font-size: 52px; }
  .card--front .wordmark { top: 70px; font-size: 44px; }

  .divider {
    position: absolute; left: 70px; right: 50px; top: 160px;
    height: 1.5px; background: var(--gold);
  }

  .holder {
    position: absolute; left: 48px; top: 200px;
    padding-left: 22px; border-left: 5px solid var(--gold);
    font-family: "Montserrat", sans-serif;
  }
  .holder__name {
    color: var(--gold); font-weight: 600; font-size: 26px;
    letter-spacing: 1px; line-height: 1.15;
  }
  .holder__title {
    color: var(--soft-white); font-weight: 400; font-size: 19px; margin-top: 4px;
  }

  .contacts {
    position: absolute; right: 40px; top: 250px;
    list-style: none; font-family: "Montserrat", sans-serif;
    font-size: 19px; color: var(--white); text-align: right;
  }
  .contacts li {
    display: flex; justify-content: flex-end; align-items: center;
    gap: 12px; height: 29px;
  }
  .contacts svg { width: 18px; height: 18px; flex: none; }
  .accent { color: var(--gold); }

  .base-bands {
    position: absolute; left: 0; bottom: 0; width: 700px; height: 40px;
  }
</style>
</head>
<body>
<main class="canvas">

  <section class="card card--back" aria-label="Card back">
    <p class="wordmark">BRISKEL</p>
  </section>

  <section class="card card--front" aria-label="Card front">
    <p class="wordmark">BRISKEL</p>
    <div class="divider"></div>

    <div class="holder">
      <p class="holder__name">TOBIAS FENNICK</p>
      <p class="holder__title">Co-Founder | Project Manager</p>
    </div>

    <ul class="contacts">
      <li>555-318-7094
        <svg viewBox="0 0 20 20" fill="none" stroke="var(--gold)" stroke-width="1.5"><circle cx="10" cy="10" r="8.5"/><path d="M7 6.5c0 4 2.5 6.5 6.5 6.5l.5-1.8-2-.8-1 1c-1.2-.6-2-1.4-2.6-2.6l1-1-.8-2z"/></svg>
      </li>
      <li>555-642-1586
        <svg viewBox="0 0 20 20" fill="none" stroke="var(--gold)" stroke-width="1.5"><rect x="6" y="2" width="8" height="16" rx="1.5"/><line x1="9" y1="15" x2="11" y2="15"/></svg>
      </li>
      <li>Tobias@briskel-example.ca
        <svg viewBox="0 0 20 20" fill="none" stroke="var(--gold)" stroke-width="1.5"><rect x="2" y="5" width="16" height="11"/><path d="M2 5l8 6 8-6"/></svg>
      </li>
      <li><span>WWW.<span class="accent">BRISKEL</span>.CA</span>
        <svg viewBox="0 0 20 20" fill="none" stroke="var(--gold)" stroke-width="1.5"><circle cx="10" cy="10" r="8"/><ellipse cx="10" cy="10" rx="3.5" ry="8"/><line x1="2" y1="10" x2="18" y2="10"/></svg>
      </li>
    </ul>

    <svg class="base-bands" viewBox="0 0 700 40" aria-hidden="true">
      <polygon points="0,0 240,0 262,40 0,40" fill="var(--gold)"/>
      <polygon points="270,22 700,22 700,40 278,40" fill="var(--white)"/>
    </svg>
  </section>

</main>
</body>
</html>
```